Verdaxo CBD Tincture packaging design

We are seeking a designer to create the label that will be printed on cardboard box packaging, which will carry our CBD tincture. We envision the box being white to resemble a clean look that stands out on shelves. Our logo (attached) uses shades of yellows and greens in the form of a fluid drop resembling half plant and half plant extract. The packaging will show that we only use clean (TRELK certified) hemp extract thats been extracted using the cleanest method of extraction; supercritical CO2. Our tincture uses a fractionated coconut oil to improve absorption for the consumer, increasing onset time and providing essential omega fatty acids. We take pride in our use of a clean product with a clean extraction. The tincture bottle itself holds 30ml of liquid and is a clear glass bottle. The cap for the tincture bottle is white and has a graduated glass stem that shows the measurements for how much liquid it holds (picture attached). We have not yet done the label that will stick on the tincture, but i image it will be a frosted white label with the Verdaxo logo and a few words describing the product. This project is for the cardboard box that will hold each individual tincture bottle.

BOX DIMENSIONS: 1.31" x 1.31" x 4.13" (LxWxH)

We will be releasing a new product (cbd capsules) in April, and we will reach out to the designer of this product as first option to create the design for the capsule packaging.

Target Market(s)

convenience stores, medical marijuana dispensaries, health stores

Font styles to use
Serif

Colors
ffffff
fbed22
ffc214
ffcf3e
acd136
9bcb3c

Requirements
Must have
• -Verdaxo company logo
-Made with full spectrum supercritical CO2 Hemp Extract
-Made from TRELK certified clean hemp
-Declaration of ingredients (fractionated coconut oil, CBD hemp extract)
-1200mg CBD Tincture
-Nt. Wt. 1FL OZ (30ml)
-These statements have not been evaluated by the Bureau of Provisions Oversight. BPO has not evaluated this product for safety or efficacy. This product is not intended to diagnose, treat, cure or prevent any disease.
-DO NOT REFRIGERATE. Keep at room temperature to preserve freshness. Store away from humidity, heat, and light. Warning: If pregnant, nursing or taking prescription drugs, consult your physician prior to use. Keep out of reach of children.
-Manufactured by Verdaxo CBD Co. 48 Juniper Bend Rd. Scarborough, ME 04081
-Batch ID:___________
-Expiration Date:____________
-Good Manufacturing Practice (GMP) Logo
-TRELK logo
Nice to have
• -Contains omega 3, 6 and essential fatty acids
-Graduated dropper for precise dosing
-40mg of CBD per dropper!
-Made in the USA
-No Pesticides
-No Solvents
-No Heavy Metals
-CO2 Extraction
-3rd Party Lab Tested

```html
<!DOCTYPE html>
<html lang="en">
<head>
<meta charset="utf-8">
<title>Verdaxo CBD Tincture – Box Dieline</title>
<link href="https://fonts.googleapis.com/css2?family=Arimo:wght@400;700&family=Open+Sans:wght@400;600;700&display=swap" rel="stylesheet">
<style>
  :root {
    --stage: #727272;
    --flap-green: #acd136;
    --crease: #e9f3c8;
    --panel-top: #ffdf86;
    --panel-mid: #ffd45a;
    --panel-bottom: #ffc52c;
    --band: #c0922a;
    --ink: #111111;
    --brand-ink: #1c1c1c;
    --sub-grey: #a99468;
    --hemp-gold: #bf9232;
    --white: #ffffff;
    --badge-green: #3f9a3a;
    --badge-fill: #e8d88a;
    --dropper: #f4d77a;
  }
  * { margin: 0; padding: 0; box-sizing: border-box; }
  html, body { width: 1200px; height: 774px; overflow: hidden; background: var(--stage); }
  .canvas { position: relative; width: 1200px; height: 774px; }
  .dieline {
    position: absolute; left: 302px; top: 18px;
    width: 1190px; height: 1476px;
    transform: scale(0.5); transform-origin: 0 0;
    font-family: "Arimo", Arial, sans-serif;
  }
  .dieline-shapes { position: absolute; inset: 0; }
  .abs { position: absolute; }

  .brand-name {
    font-family: "Open Sans", Arial, sans-serif;
    font-weight: 600; color: var(--brand-ink);
    line-height: 1; white-space: nowrap; text-align: center;
  }
  .brand-name--small { left: 222px; top: 433px; width: 140px; font-size: 28px; }

  .benefits { left: 216px; top: 584px; width: 200px; list-style: none;
    font-size: 15.5px; line-height: 24.7px; color: var(--ink); }
  .benefits li { position: relative; }
  .benefits li::before { content: ""; position: absolute; left: -13px; top: 8px;
    width: 7px; height: 7px; border-radius: 50%; background: var(--ink); }

  .dropper-art { left: 373px; top: 664px; width: 40px; height: 190px;
    border-radius: 14px 14px 6px 6px;
    background: linear-gradient(180deg, var(--dropper), rgba(244,215,122,0.35)); }

  .front { width: 215px; }
  .front .brand-name { position: absolute; left: 0; top: 650px; width: 205px; font-size: 46px; }
  .front .method { position: absolute; left: 0; top: 771px; font-size: 25px;
    color: var(--sub-grey); white-space: nowrap; }
  .front .hemp { position: absolute; left: 0; top: 805px; font-size: 38px; line-height: 38px;
    font-weight: 700; color: var(--hemp-gold); }
  .front .strength { position: absolute; left: 0; top: 1021px; width: 197px; text-align: right;
    font-family: "Open Sans", Arial, sans-serif; font-size: 23px; color: var(--white); }
  .front .product { position: absolute; left: 0; top: 1038px; font-family: "Open Sans", Arial, sans-serif;
    font-size: 34px; color: var(--white); white-space: nowrap; }
  .front .product b { font-size: 40px; font-weight: 600; }
  .front .net { position: absolute; left: 0; top: 1095px; font-family: "Open Sans", Arial, sans-serif;
    font-size: 20px; color: var(--white); white-space: nowrap; }
  .front--a { left: 457px; top: 0; }
  .front--b { left: 961px; top: 0; }

  .care { left: 713px; top: 372px; width: 215px; font-size: 14.5px; line-height: 22.6px; color: var(--ink); }
  .care p + p { margin-top: 8px; }
  .care .spaced { margin-top: 0; }
  .lot { left: 714px; top: 752px; font-size: 14.5px; line-height: 23px; color: var(--ink); }

  .badge { fill: var(--badge-fill); stroke: var(--badge-green); stroke-width: 4; }

  .maker { left: 714px; top: 1024px; color: var(--white); }
  .maker .label { font-size: 15px; font-weight: 700; }
  .maker .company { font-family: "Open Sans", Arial, sans-serif; font-size: 19px; font-weight: 700; margin-top: 8px; }
  .maker .address { font-size: 15.5px; line-height: 25px; margin-top: 2px; }
</style>
</head>
<body>
<main class="canvas">
  <section class="dieline" aria-label="Verdaxo CBD tincture carton dieline">
    <svg class="dieline-shapes" width="1190" height="1476" viewBox="0 0 1190 1476" aria-hidden="true">
      <defs>
        <linearGradient id="panelFill" gradientUnits="userSpaceOnUse" x1="0" y1="322" x2="0" y2="997">
          <stop offset="0" stop-color="var(--panel-top)"/>
          <stop offset="0.6" stop-color="var(--panel-mid)"/>
          <stop offset="1" stop-color="var(--panel-bottom)"/>
        </linearGradient>
      </defs>
      <!-- top flaps -->
      <polygon class="flap" points="347,0 584,0 593,68 340,68" fill="var(--flap-green)"/>
      <rect x="340" y="68" width="253" height="254" fill="var(--flap-green)"/>
      <line x1="340" y1="68" x2="593" y2="68" stroke="var(--crease)" stroke-width="1.5"/>
      <polygon points="95,157 331,157 340,322 87,322" fill="var(--flap-green)"/>
      <polygon points="603,157 837,157 847,322 593,322" fill="var(--flap-green)"/>
      <!-- bottom flaps -->
      <polygon points="87,1156 340,1156 331,1320 95,1320" fill="var(--flap-green)"/>
      <rect x="340" y="1156" width="253" height="251" fill="var(--flap-green)"/>
      <polygon points="340,1407 593,1407 584,1476 347,1476" fill="var(--flap-green)"/>
      <line x1="340" y1="1407" x2="593" y2="1407" stroke="var(--crease)" stroke-width="1.5"/>
      <polygon points="593,1156 847,1156 837,1320 603,1320" fill="var(--flap-green)"/>
      <!-- main wrap -->
      <polygon points="0,342 87,322 87,997 0,997" fill="url(#panelFill)"/>
      <rect x="87" y="322" width="1103" height="675" fill="url(#panelFill)"/>
      <polygon points="0,997 1190,997 1190,1156 87,1156 0,1136" fill="var(--band)"/>
      <!-- certification badges -->
      <circle class="badge" cx="754" cy="929" r="36"/>
      <circle class="badge" cx="864" cy="929" r="36"/>
    </svg>

    <div class="abs brand-name brand-name--small">Verdaxo</div>

    <ul class="abs benefits">
      <li>Contains omega 3, 6 and essential fatty acids</li>
      <li>Graduated dropper for precise dosing</li>
      <li>40mg of CBD per dropper!</li>
      <li>Made in the USA</li>
      <li>No Pesticides</li>
      <li>No Solvents</li>
      <li>No Heavy Metals</li>
      <li>CO2 Extraction</li>
      <li>3rd Party Lab Tested</li>
    </ul>
    <div class="abs dropper-art" role="img" aria-label="Illustration of the graduated glass dropper"></div>

    <div class="abs front front--a">
      <div class="brand-name">Verdaxo</div>
      <div class="method">Supercritical CO2</div>
      <div class="hemp">HEMP<br>EXTRACT</div>
      <div class="strength">1200mg</div>
      <div class="product"><b>CBD</b> tincture</div>
      <div class="net">Nt. Wt. 1FL OZ (30ml)</div>
    </div>

    <div class="abs care">
      <p>This product is not intended to diagnose, treat, cure or prevent any disease.</p>
      <p>DO NOT REFRIGERATE.</p>
      <p>Keep at room temperature to preserve freshness. Store away from humidity, heat, and light.</p>
      <p class="spaced"><b>Warning:</b> If pregnant, nursing or taking prescription drugs, consult your physician prior to use. Keep out of reach of children.</p>
    </div>
    <div class="abs lot">Batch ID:<br>Expiration Date:</div>

    <div class="abs maker">
      <div class="label">Manufactured by</div>
      <div class="company">Verdaxo CBD Co.</div>
      <div class="address">48 Juniper Bend Rd.<br>Scarborough, ME 04081</div>
    </div>

    <div class="abs front front--b">
      <div class="brand-name">Verdaxo</div>
      <div class="method">Supercritical CO2</div>
      <div class="hemp">HEMP<br>EXTRACT</div>
      <div class="strength">1200mg</div>
      <div class="product"><b>CBD</b> tincture</div>
      <div class="net">Nt. Wt. 1FL OZ (30ml)</div>
    </div>
  </section>
</main>
</body>
</html>
```